Podcast Cover Art for rebranded podcast - I have inspiration for the designs

I've had a podcast ("Paperboat Radio Hour") since 2018, but I'm in the process of rebranding it. I've attached the old cover art below, which I loved, but I don't need it to look like that at all. The rebranded podcast is called 'Open Window with Marnie Cole.' I've included the show description at the bottom. I've been working on various design options in Canva, but not obsessed with anything yet, but I'm attaching the ones I do like that I think just need some refining. My very favorite is the one labeled 'favorite_Open Window' so I wouldn't mind keeping that general idea but perfected by a designer. Ultimately, I want something cool, fairly clean, modern, eye catching. I'm into neutrals with maybe a pop of color, so think black, white, grey..maybe silver, and I love a pop of red..and I'm not opposed to other options for the pop color. The show is going to be inspiring, entertaining, and funny. Oh and one other idea I had but I'm not sure if it makes sense with the title and/or what the show is about..but a vinyl record with Open Window with Marnie Cole on it somehow, on a record player..not sure.

Ever wonder what it means to truly live authentically? Curious about how to embrace the unpredictability of life? Ready for some heartfelt and lighthearted conversations that inspire and entertain?
Join Marnie Cole as she dives into the raw, real, and unscripted moments of life. In each episode, Marnie brings candid conversations and genuine insights into the ups and downs we all experience. From personal growth and self-discovery to inspiring stories and valuable life lessons, "Open Window" is a space where authenticity reigns and spontaneity is celebrated.
Whether she's sharing her own journey or chatting with inspiring guests, Marnie invites you to explore the beauty of living life without a script. Expect honest reflections, thought-provoking discussions, and a refreshing perspective on navigating life's unpredictable path—all with a dash of fun and humor to keep things lively and entertaining. Step into the unscripted moments of life and tune in for a blend of depth and lightheartedness that will leave you inspired, smiling, and most importantly laughing.

Target Market(s)

25-50 year old women and men (primarily women)

Font styles to use
Sans Serif

Requirements
Should not have
• nothing too feminine or girly, nothing cheesy :)

```html
<!DOCTYPE html>
<html lang="en">
<head>
<meta charset="utf-8">
<title>Open Window with Marnie Cole – Podcast Cover</title>
<link rel="stylesheet" href="https://fonts.googleapis.com/css2?family=Anton&family=Kaushan+Script&family=Montserrat:wght@300;500&display=swap">
<style>
  :root {
    --navy-top: #030a3c;
    --navy-deep: #010c2c;
    --navy-band: #07125a;
    --navy-glow: #0d4f92;
    --cyan: #12dcd3;
    --cyan-text: #22d6d2;
    --yellow: #ffd400;
    --white: #ffffff;
  }
  html, body {
    margin: 0;
    padding: 0;
    width: 1200px;
    height: 1200px;
    overflow: hidden;
    background: var(--navy-top);
  }
  .cover {
    position: relative;
    width: 1200px;
    height: 1200px;
    overflow: hidden;
    background: linear-gradient(180deg, #020834 0%, var(--navy-top) 55%, #06206a 85%, var(--navy-glow) 100%);
  }
  .cover svg { position: absolute; inset: 0; }
  .title-main {
    font-family: 'Anton', 'Arial Narrow', sans-serif;
    fill: var(--white);
  }
  .title-script {
    font-family: 'Kaushan Script', cursive;
    fill: var(--yellow);
  }
  .host-with {
    font-family: 'Montserrat', sans-serif;
    font-weight: 500;
    fill: var(--white);
    letter-spacing: 6px;
  }
  .host-name {
    font-family: 'Montserrat', sans-serif;
    font-weight: 300;
    fill: var(--cyan-text);
  }
  .accent { fill: var(--cyan); }
</style>
</head>
<body>
<main class="cover">
  <svg width="1200" height="1200" viewBox="0 0 1200 1200" xmlns="http://www.w3.org/2000/svg">
    <defs>
      <linearGradient id="host-photo-tone" x1="0" y1="0" x2="0" y2="1">
        <stop offset="0" stop-color="#c9a08a"/>
        <stop offset="0.45" stop-color="#4a2c22"/>
        <stop offset="1" stop-color="#1d2a2a"/>
      </linearGradient>
      <linearGradient id="bottom-haze" x1="0" y1="0" x2="0" y2="1">
        <stop offset="0" stop-color="#061a5e" stop-opacity="0"/>
        <stop offset="1" stop-color="#0e5a9c"/>
      </linearGradient>
    </defs>

    <!-- dark panels -->
    <rect class="panel-left" x="0" y="401" width="613" height="500" fill="var(--navy-deep)"/>
    <rect class="panel-wide" x="0" y="496" width="1200" height="491" fill="var(--navy-deep)"/>
    <rect class="host-band" x="0" y="891" width="552" height="94" fill="var(--navy-band)"/>
    <rect class="bottom-haze" x="0" y="985" width="1200" height="215" fill="url(#bottom-haze)"/>

    <!-- host photograph area -->
    <rect class="host-photo" role="img" aria-label="Photo of the host, arms raised, smiling, long dark hair, dark t-shirt"
          x="700" y="34" width="342" height="951" rx="40" fill="url(#host-photo-tone)" opacity="0.85"/>

    <!-- cyan accent stripes, top -->
    <polygon class="accent" points="0,262 646,58 626,80 0,282"/>
    <polygon class="accent" points="235,175 619,97 602,119 219,191"/>
    <polygon class="accent" points="9,316 190,260 180,270 9,326"/>

    <!-- cyan accent stripes, bottom -->
    <polygon class="accent" points="440,1074 1200,869 1200,885 428,1090"/>
    <polygon class="accent" points="633,1069 1200,905 1200,927 620,1083"/>
    <polygon class="accent" points="870,941 1040,905 1036,914 866,950"/>

    <!-- title -->
    <text class="title-main" x="109" y="639" font-size="330"
          textLength="523" lengthAdjust="spacingAndGlyphs">OPEN</text>
    <text class="title-script" x="150" y="752" font-size="150" transform="rotate(-4 300 720)">Window</text>

    <!-- host -->
    <text class="host-with" x="99" y="889" font-size="34">WITH</text>
    <text class="host-name" x="97" y="966" font-size="76">Marnie Cole</text>
  </svg>
</main>
</body>
</html>
```